Torvel’s letterhead for local government

I require a letterhead for quarterly communications with constituents. The colours I have used in the past are navy & green (together) so I’m happy to use similar colours for this. Please refer to business card as an example.
The letter must make reference to the position I hold which is as per below
“Clr Torvel Quennisbury OAM”
And the tag line I have used in the past is “Torvel on the Terrace”. Although I’m not sure if this would be used in a letterhead or not. Happy for this to be provided as an option.
I would like a photo in the letterhead as I believe face recognition is key as an elected member.

Target Market(s)

Political interests

Industry/Entity Type

Government Office

Font styles to use
Sans Serif

Requirements
Must have
• Politically professional. I have been an elected member for 2 years so it is expected that the letterhead conveys that. The colours of the business card is to be used.
Nice to have
• Background of photos to be manipulated or changed to make me stand out, if possible?
Should not have
• Looked like it’s cropped or undertaken by an amateur designer.

```html
<!DOCTYPE html>
<html lang="en">
<head>
<meta charset="utf-8">
<title>Torvel Quennisbury – Letterhead</title>
<link href="https://fonts.googleapis.com/css2?family=Arimo:wght@400;700&family=Open+Sans:wght@400;600&display=swap" rel="stylesheet">
<style>
  :root {
    --navy: #2a5d8f;
    --green: #3dba6a;
    --paper: #ffffff;
    --backdrop: #e4e4e4;
    --ink: #4a4a4a;
    --ink-strong: #333333;
    --photo-light: #9fb3c6;
    --photo-dark: #2f3b4b;
  }
  * { margin: 0; padding: 0; box-sizing: border-box; }
  html, body {
    width: 1040px; height: 1200px; overflow: hidden;
    background: var(--backdrop);
  }
  .letterhead {
    position: absolute; left: 53px; top: 0;
    width: 790px; height: 1016px;
    background: var(--paper);
    transform: scale(1.1811);
    transform-origin: top left;
    font-family: "Open Sans", sans-serif;
    color: var(--ink);
  }
  .letterhead__shapes { position: absolute; inset: 0; }
  .header__name {
    position: absolute; left: 298px; top: 60px;
    font-family: "Arimo", sans-serif; font-weight: 700;
    font-size: 23px; color: var(--green); letter-spacing: 0.2px;
  }
  .header__role {
    position: absolute; left: 298px; top: 97px;
    font-family: "Arimo", sans-serif; font-size: 17.5px;
    line-height: 22px; color: #fff;
  }
  .letter { position: absolute; left: 75px; width: 638px; font-size: 12.6px; }
  .letter__date { top: 216px; }
  .letter__recipient { top: 246px; line-height: 15.5px; }
  .letter__salutation { top: 335px; }
  .letter__body p { text-align: justify; line-height: 23px; hyphens: auto; }
  .letter__body--one { top: 378px; }
  .letter__body--two { top: 515px; }
  .letter__body--three { top: 606px; }
  .letter__closing { top: 722px; }
  .letter__signatory { top: 787px; }
  .signatory__name { font-size: 15.5px; font-weight: 600; color: var(--ink-strong); }
  .signatory__title { font-size: 12.6px; margin-top: 3px; }
  .footer__contacts {
    position: absolute; left: 91px; top: 980px;
    font-family: "Arimo", sans-serif; font-size: 15px; color: #fff;
    white-space: nowrap;
  }
  .footer__contacts b { font-weight: 700; }
  .footer__divider { margin: 0 12px; }
</style>
</head>
<body>
<div class="letterhead">
  <svg class="letterhead__shapes" width="790" height="1016" viewBox="0 0 790 1016">
    <defs>
      <linearGradient id="portraitTone" x1="0" y1="0" x2="0" y2="1">
        <stop offset="0" stop-color="var(--photo-light)"/>
        <stop offset="1" stop-color="var(--photo-dark)"/>
      </linearGradient>
    </defs>
    <polygon class="header__band" points="0,0 790,0 790,137 0,180" fill="var(--navy)"/>
    <polygon class="header__accent" points="0,182 790,142 790,164 0,184" fill="var(--green)"/>
    <rect class="header__portrait" x="127" y="15" width="132" height="157" rx="4"
          fill="url(#portraitTone)" role="img" aria-label="Portrait photo of Clr Torvel Quennisbury in a dark suit and tie"/>
    <polygon class="footer__accent" points="0,927 790,953 790,968 0,929" fill="var(--green)"/>
    <polygon class="footer__band" points="0,935 790,974 790,1016 0,1016" fill="var(--navy)"/>
  </svg>

  <div class="header__name">Clr Torvel Quennisbury OAM</div>
  <div class="header__role">Candidate for Area Councillor<br>City of Harrowgate</div>

  <div class="letter letter__date">Issuing Date: May 5, 2018</div>
  <div class="letter letter__recipient">Name Of Employee Mr. Hollis Verane<br>Address of Employee<br>Address Line 2 etc..</div>
  <div class="letter letter__salutation">Dear Mr. Verane</div>

  <div class="letter letter__body letter__body--one"><p>Lorem Ipsum has been the industry's standard dummy text ever since the 1500s, when an unknown printer took a galley of type and scrambled it to make a type specimen book. It has survived not only five centuries, but also the leap into electronic typesetting, remaining essentially unchanged. It was popularised in the 1960s with the release of Vellumset sheets containing Lorem Ipsum passages, and more recently with desktop publishing software like Orlen Leafmaker including versions of Lorem Ipsum.</p></div>
  <div class="letter letter__body letter__body--two"><p>Lorem Ipsum is simply dummy text of the printing and typesetting industry. Lorem Ipsum has been the industry's standard dummy text ever since the 1500s, when an unknown printer took a galley of type and scrambled it to make a type specimen book.</p></div>
  <div class="letter letter__body letter__body--three"><p>It has survived not only five centuries, but also the leap into electronic typesetting, remaining essentially unchanged. It was popularised in the 1960s with the release of Vellumset sheets containing Lorem IpsumIpsum passages.</p></div>

  <div class="letter letter__closing">Yours Sincerely</div>
  <div class="letter letter__signatory">
    <div class="signatory__name">Marden Ellcott</div>
    <div class="signatory__title">Managing Director</div>
  </div>

  <div class="footer__contacts"><b>P:</b> 044-555 018 274<span class="footer__divider">|</span><b>E:</b> hello@torvelcouncil.org<span class="footer__divider">|</span>www.torvelcouncil.org</div>
</div>
</body>
</html>
```